Business Card Design

We need a business card designed for our new company. Prefer a black card with white logo & writing.

Contact Information for Business Card

Ted Galloway, address: 7-4812 Fernhollow Road, Abbotsford, BC, V3K 8R2, Office Phone: 604-712-3390, Cell: 604-947-2164, Email: ted@resinworkshub.ca

Colors

Designer to choose only greyscale colors for use in the design.

```html
<!DOCTYPE html>
<html lang="en">
<head>
<meta charset="UTF-8">
<title>Resinworks Hub – Business Card</title>
<link rel="stylesheet" href="https://fonts.googleapis.com/css2?family=Poppins:wght@300;400;700&display=swap">
<style>
  :root {
    --backdrop: #1f1f20;
    --card: #232326;
    --ink: #ffffff;
    --ink-soft: #d9d9d9;
    --accent: #f4f2ea;
  }
  * { margin: 0; padding: 0; box-sizing: border-box; }
  html, body {
    width: 1200px; height: 711px; overflow: hidden;
    background: var(--backdrop);
    font-family: "Poppins", sans-serif;
    color: var(--ink);
  }
  .stage {
    position: relative; width: 1200px; height: 711px;
    display: flex; align-items: center; justify-content: center; gap: 40px;
  }
  .card {
    position: relative; width: 540px; height: 309px;
    background: var(--card); border-radius: 22px; overflow: hidden;
    box-shadow: 0 10px 30px rgba(0,0,0,.45);
  }
  .brand {
    display: flex; align-items: center; gap: 12px;
    font-weight: 700; text-transform: uppercase; letter-spacing: 1px;
    color: var(--ink); white-space: nowrap;
  }
  .brand-mark { width: 16px; height: 16px; background: var(--ink); flex: none; }
  .card-front .brand {
    position: absolute; inset: 0; justify-content: center; font-size: 34px;
  }
  .card-back .brand {
    position: absolute; left: 40px; top: 112px; font-size: 22px;
  }
  .card-back .brand-mark { width: 14px; height: 14px; }
  .accent-bar {
    position: absolute; right: 0; top: 32px; width: 28px; height: 52px;
    background: var(--accent);
  }
  .person {
    position: absolute; right: 40px; top: 34px; text-align: right;
  }
  .person-name { font-size: 30px; line-height: 1.1; white-space: nowrap; }
  .person-name .first { font-weight: 700; }
  .person-name .last { font-weight: 300; }
  .person-role { font-size: 13px; font-weight: 400; color: var(--ink-soft); }
  .address {
    position: absolute; right: 30px; top: 176px; text-align: right;
    font-size: 13px; font-weight: 300; font-style: normal; line-height: 1.45;
  }
  .contacts {
    position: absolute; left: 40px; bottom: 26px; list-style: none;
    font-size: 13px; font-weight: 300; line-height: 1.55;
  }
  .contacts li { display: flex; align-items: center; gap: 10px; }
  .contacts svg { width: 12px; height: 12px; fill: none; stroke: var(--ink); stroke-width: 1.6; flex: none; }
</style>
</head>
<body>
<main class="stage">
  <section class="card card-front" aria-label="Card front">
    <div class="brand"><span class="brand-mark"></span>Resinworks Hub</div>
  </section>

  <section class="card card-back" aria-label="Card back">
    <div class="brand"><span class="brand-mark"></span>Resinworks Hub</div>
    <div class="accent-bar"></div>
    <div class="person">
      <p class="person-name"><span class="first">Ted</span> <span class="last">Galloway</span></p>
      <p class="person-role">Founder &amp; CEO</p>
    </div>
    <address class="address">
      7-4812 Fernhollow Road,<br>Abbotsford, BC, V3K 8R2.
    </address>
    <ul class="contacts">
      <li><svg viewBox="0 0 12 12"><path d="M2 1.5l2 .3.8 2.2-1.3 1a6 6 0 0 0 3.5 3.5l1-1.3 2.2.8.3 2A1 1 0 0 1 9.5 11 8.5 8.5 0 0 1 1 2.5a1 1 0 0 1 1-1z"/></svg>604-712-3390</li>
      <li><svg viewBox="0 0 12 12"><rect x="3" y="1" width="6" height="10" rx="1"/><path d="M5.5 9h1"/></svg>604-947-2164</li>
      <li><svg viewBox="0 0 12 12"><circle cx="6" cy="6" r="5"/><path d="M1 6h10M6 1c2 2.5 2 7.5 0 10M6 1c-2 2.5-2 7.5 0 10"/></svg>www.resinworkshub.ca</li>
      <li><svg viewBox="0 0 12 12"><rect x="1" y="2.5" width="10" height="7" rx="1"/><path d="M1 3l5 3.5L11 3"/></svg>ted@resinworkshub.ca</li>
    </ul>
  </section>
</main>
</body>
</html>
```